Veltrano.co - Polar Expeditions Specialists

We need a modern, visually striking business card for Veltrano.co, a company specialized in selling expedition cruises to the most remote regions on Earth, with a focus on the Arctic and Antarctica. The design should instantly communicate that the cardholder is an expert in polar travel. Use clean, premium aesthetics with cool tones like icy blue and white, possibly incorporating polar imagery (ice, glaciers, penguins, etc.)

Attached the logo

Contact Information for Business Card

Feels high-end and trustworthy.. Visually memorable — encourages people to keep it

Colors
0054AA
0677BA
7BADD7
CADEEF
E8F1F8

Requirements
Must have
• ice, glaciers, penguins, montains
Nice to have
• modern, transparente,

```html
<!DOCTYPE html>
<html lang="en">
<head>
<meta charset="utf-8">
<title>Veltrano.co – Business Card</title>
<link href="https://fonts.googleapis.com/css2?family=Poppins:wght@600;700&family=Montserrat:wght@400;500&display=swap" rel="stylesheet">
<style>
  :root{
    --deep:#0054AA;
    --brand:#3273B8;
    --mid:#0677BA;
    --sky:#7BADD7;
    --frost:#CADEEF;
    --ice:#E8F1F8;
    --ink:#1a1a1a;
    --paper:#ffffff;
    --stage:#e6ebf1;
  }
  *{box-sizing:border-box;margin:0;padding:0}
  html,body{width:1200px;height:1200px;overflow:hidden}
  body{background:var(--stage);font-family:"Montserrat",sans-serif;position:relative}

  .card{position:absolute;left:150px;width:900px;height:514px;border-radius:34px;overflow:hidden;box-shadow:0 10px 30px rgba(0,0,0,.15)}
  .card--back{top:60px}
  .card--front{top:626px;background:var(--paper)}

  /* back */
  .pattern-field{position:absolute;inset:0;
    background:linear-gradient(115deg,var(--sky) 0%,#4f86c4 35%,#2e62a8 65%,#1f4f98 100%)}
  .back-brand{position:absolute;left:420px;top:215px}
  .back-brand .brand-name{font-family:"Poppins",sans-serif;font-weight:700;font-size:64px;color:var(--ice);line-height:1}
  .back-brand .brand-tag{font-family:"Poppins",sans-serif;font-weight:600;font-size:19px;color:var(--frost);margin-top:8px}

  /* front */
  .brand-mark{position:absolute;left:70px;top:90px;width:130px;height:130px;border-radius:50%;background:var(--brand)}
  .front-brand{position:absolute;left:230px;top:62px}
  .front-brand .brand-name{font-family:"Poppins",sans-serif;font-weight:700;font-size:100px;line-height:1;color:var(--brand)}
  .front-brand .brand-tag{font-family:"Poppins",sans-serif;font-weight:600;font-size:27px;color:var(--brand);margin-top:6px;padding-left:40px}

  .holder{position:absolute;left:190px;top:250px;text-align:right;width:290px}
  .holder .holder-name{font-family:"Poppins",sans-serif;font-weight:700;font-size:32px;color:var(--brand);white-space:nowrap;line-height:1.2}
  .holder .holder-role{font-size:19px;color:var(--ink);margin-top:4px}
  .divider{position:absolute;left:503px;top:246px;width:2px;height:108px;background:var(--brand)}
  .contacts{position:absolute;left:524px;top:240px;list-style:none}
  .contacts li{display:flex;align-items:center;gap:12px;font-size:20px;color:var(--ink);height:38px}
  .contacts svg{width:19px;height:19px;fill:var(--brand);flex:none}

  .wave{position:absolute;left:0;top:0;width:900px;height:514px}
</style>
</head>
<body>

<section class="card card--back" aria-label="Card back">
  <div class="pattern-field" role="img" aria-label="Repeating pattern of the brand symbol in graded icy blues"></div>
  <div class="back-brand">
    <div class="brand-name">Veltrano.co</div>
    <div class="brand-tag">Polar Expeditions Specialists</div>
  </div>
</section>

<section class="card card--front" aria-label="Card front">
  <svg class="wave" viewBox="0 0 900 514" aria-hidden="true">
    <path d="M0 514 L0 505 C150 430 350 410 540 402 C720 395 830 335 900 250 L900 514 Z" fill="var(--brand)"/>
    <path d="M330 430 C500 405 700 400 900 275 L900 283 C700 410 500 415 330 430 Z" fill="var(--paper)"/>
    <path d="M640 388 C770 372 850 310 900 215 L900 232 C850 325 770 382 640 388 Z" fill="var(--brand)"/>
  </svg>

  <div class="brand-mark" aria-hidden="true"></div>
  <div class="front-brand">
    <div class="brand-name">Veltrano.co</div>
    <div class="brand-tag">Polar Expeditions Specialists</div>
  </div>

  <div class="holder">
    <div class="holder-name">Marco Ellison</div>
    <div class="holder-role">Managing Director</div>
  </div>
  <div class="divider"></div>
  <ul class="contacts">
    <li><svg viewBox="0 0 24 24"><path d="M6.6 10.8a15 15 0 0 0 6.6 6.6l2.2-2.2a1 1 0 0 1 1-.25 11.4 11.4 0 0 0 3.6.57 1 1 0 0 1 1 1V20a1 1 0 0 1-1 1A17 17 0 0 1 3 4a1 1 0 0 1 1-1h3.5a1 1 0 0 1 1 1c0 1.25.2 2.45.57 3.6a1 1 0 0 1-.25 1z"/></svg>(555)214-7730</li>
    <li><svg viewBox="0 0 24 24"><path d="M2 5h20v14H2z"/><path d="M3 6l9 7 9-7" stroke="#fff" stroke-width="1.6" fill="none"/></svg>info@veltrano.co</li>
    <li><svg viewBox="0 0 24 24"><circle cx="12" cy="12" r="10"/><path d="M2 12h20M12 2c3 3 3 17 0 20M12 2c-3 3-3 17 0 20" stroke="#fff" stroke-width="1.4" fill="none"/></svg>www.veltrano.co</li>
  </ul>
</section>

</body>
</html>
```